landscaping core flute signs

I need core flutes created with business name and a few extra dot points for putting on fences for job sites 120cm x 120cm approx.
I want our old ones information with the new L logo and colour palette

```html
<!DOCTYPE html>
<html lang="en">
<head>
<meta charset="utf-8">
<title>Grounded Terrace – Fence Sign</title>
<link href="https://fonts.googleapis.com/css2?family=Cinzel:wght@500;600&family=Poppins:wght@600;700;800&display=swap" rel="stylesheet">
<style>
  :root {
    --backdrop: #545454;
    --sign-white: #ffffff;
    --brand-green: #5f8f58;
    --check-green: #4a9b4a;
    --ink: #0b0b0b;
    --pill-border-green: #5f8f58;
  }
  html, body {
    margin: 0;
    padding: 0;
    width: 671px;
    height: 1200px;
    overflow: hidden;
    background: var(--backdrop);
  }
  .canvas {
    position: relative;
    width: 671px;
    height: 1200px;
  }
  .sign {
    position: absolute;
    left: 35px;
    top: 300px;
    width: 600px;
    height: 600px;
    background: var(--sign-white);
    overflow: hidden;
    box-shadow: 0 4px 14px rgba(0,0,0,0.35);
  }
  .contact-band {
    position: absolute;
    left: 0;
    top: 373px;
    width: 600px;
    height: 227px;
    background: var(--brand-green);
  }
  .brand {
    position: absolute;
    left: 58px;
    top: 37px;
    display: flex;
    align-items: center;
    gap: 22px;
  }
  .brand-dot {
    width: 120px;
    height: 120px;
    border-radius: 50%;
    background: var(--brand-green);
    flex: none;
  }
  .brand-text {
    display: flex;
    flex-direction: column;
    align-items: center;
  }
  .brand-name {
    font-family: "Cinzel", serif;
    font-weight: 600;
    font-size: 44px;
    line-height: 1;
    color: var(--ink);
    letter-spacing: 1px;
    text-align: center;
  }
  .brand-tagline {
    margin-top: 12px;
    font-family: "Cinzel", serif;
    font-weight: 500;
    font-size: 15px;
    letter-spacing: 4px;
    color: var(--brand-green);
  }
  .services {
    position: absolute;
    left: 40px;
    top: 198px;
    width: 522px;
    margin: 0;
    padding: 0;
    list-style: none;
  }
  .service {
    position: absolute;
    left: 0;
    width: 522px;
    height: 58px;
    box-sizing: border-box;
    border-radius: 29px;
    background: var(--sign-white);
    border: 3px solid var(--pill-border-green);
    display: flex;
    align-items: center;
    padding-left: 12px;
    gap: 16px;
    font-family: "Poppins", sans-serif;
    font-weight: 800;
    font-size: 29px;
    letter-spacing: 3.2px;
    color: var(--ink);
    white-space: nowrap;
  }
  .service--paving { top: 0; }
  .service--fencing { top: 72px; border-color: var(--ink); }
  .service--design { top: 142px; }
  .tick {
    width: 34px;
    height: 34px;
    flex: none;
  }
  .phone {
    position: absolute;
    left: 26px;
    top: 434px;
    display: flex;
    align-items: center;
    gap: 12px;
  }
  .phone-icon {
    width: 60px;
    height: 60px;
    flex: none;
  }
  .phone-number {
    font-family: "Poppins", sans-serif;
    font-weight: 800;
    font-size: 75px;
    line-height: 1;
    letter-spacing: -2px;
    color: var(--ink);
    padding-top: 8px;
    white-space: nowrap;
  }
  .email {
    position: absolute;
    left: 27px;
    top: 517px;
    display: flex;
    align-items: center;
    gap: 12px;
  }
  .email-icon {
    width: 30px;
    height: 24px;
    flex: none;
  }
  .email-address {
    font-family: "Poppins", sans-serif;
    font-weight: 700;
    font-size: 30px;
    line-height: 1;
    color: var(--sign-white);
    white-space: nowrap;
  }
  .licence-tab {
    position: absolute;
    left: 179px;
    top: 569px;
    width: 240px;
    height: 31px;
  }
  .licence-text {
    position: absolute;
    left: 179px;
    top: 569px;
    width: 240px;
    height: 31px;
    line-height: 33px;
    text-align: center;
    font-family: "Poppins", sans-serif;
    font-weight: 700;
    font-size: 15px;
    letter-spacing: 4px;
    color: var(--sign-white);
  }
</style>
</head>
<body>
<div class="canvas">
  <section class="sign" aria-label="Fence sign">
    <div class="contact-band"></div>

    <header class="brand">
      <div class="brand-dot"></div>
      <div class="brand-text">
        <div class="brand-name">GROUNDED<br>TERRACE</div>
        <div class="brand-tagline">STRUCTURAL LANDSCAPING</div>
      </div>
    </header>

    <ul class="services">
      <li class="service service--paving">
        <svg class="tick" viewBox="0 0 34 34" aria-hidden="true"><circle cx="17" cy="17" r="17" fill="var(--check-green)"/><path d="M9 17.5l5.5 5.5L25 12" fill="none" stroke="#fff" stroke-width="4" stroke-linecap="round" stroke-linejoin="round"/></svg>
        PAVING &amp; CONCRETING
      </li>
      <li class="service service--fencing">
        <svg class="tick" viewBox="0 0 34 34" aria-hidden="true"><circle cx="17" cy="17" r="17" fill="var(--ink)"/><path d="M9 17.5l5.5 5.5L25 12" fill="none" stroke="#fff" stroke-width="4" stroke-linecap="round" stroke-linejoin="round"/></svg>
        FENCING &amp; RETAINING
      </li>
      <li class="service service--design">
        <svg class="tick" viewBox="0 0 34 34" aria-hidden="true"><circle cx="17" cy="17" r="17" fill="var(--check-green)"/><path d="M9 17.5l5.5 5.5L25 12" fill="none" stroke="#fff" stroke-width="4" stroke-linecap="round" stroke-linejoin="round"/></svg>
        DESIGN &amp; CONSTRUCT
      </li>
    </ul>

    <div class="phone">
      <svg class="phone-icon" viewBox="0 0 60 60" aria-hidden="true">
        <circle cx="30" cy="30" r="30" fill="var(--ink)"/>
        <path d="M22 16c2-1 3 0 4 2l2 5c.5 1.5 0 2.5-1 3.5l-1.5 1.5c1.5 3.5 4 6 7.5 7.5l1.5-1.5c1-1 2-1.5 3.5-1l5 2c2 1 3 2 2 4l-1.5 3c-1 2-3 3-5.5 2.5C28 42 18 32 16.5 22.5 16 20 17 18 19 17z" fill="#fff"/>
        <path d="M33 18a9 9 0 0 1 9 9M33 12a15 15 0 0 1 15 15" fill="none" stroke="#fff" stroke-width="2.6" stroke-linecap="round"/>
      </svg>
      <span class="phone-number">0400 582 917</span>
    </div>

    <div class="email">
      <svg class="email-icon" viewBox="0 0 30 24" aria-hidden="true">
        <rect x="0" y="0" width="30" height="24" rx="3" fill="var(--ink)"/>
        <path d="M5 6l10 8 10-8" fill="none" stroke="var(--brand-green)" stroke-width="2.6" stroke-linecap="round" stroke-linejoin="round"/>
      </svg>
      <span class="email-address">mason@groundedterrace.com</span>
    </div>

    <svg class="licence-tab" viewBox="0 0 240 31" aria-hidden="true">
      <path d="M0 31 C10 31 14 0 34 0 H206 C226 0 230 31 240 31 Z" fill="var(--ink)"/>
    </svg>
    <div class="licence-text">QBSA: 1048263</div>
  </section>
</div>
</body>
</html>
```